Quillmere Capital LLC

Need Professional Business cards for New Investment Fund

Target Market(s)

High Quality investors

Industry/Entity Type

Financial

Contact Information for Business Card

Phone Number +1 555 284 6190
Name Lukas Varenko
Title Fund Manager
email lv@FundQuillmere.com
Website www.FundQuillmere.com

Colors

Designer to choose colors to be used in the design.

Requirements
Must have
• Must have our Logo and all of the above. Must be made so lettering and loge can be raised

```html
<!DOCTYPE html>
<html lang="en">
<head>
<meta charset="utf-8">
<title>Quillmere Capital LLC — Business Card</title>
<link href="https://fonts.googleapis.com/css2?family=Roboto+Condensed:wght@500;700&display=swap" rel="stylesheet">
<style>
  :root {
    --backdrop: #6a6b6d;
    --green-light: #88ec3a;
    --green-dark: #75d232;
    --paper: #f7f7f7;
    --ink: #3e473b;
    --band: #000000;
  }
  * { margin: 0; padding: 0; box-sizing: border-box; }
  html, body {
    width: 1200px; height: 1200px; overflow: hidden;
    background: var(--backdrop);
    font-family: "Roboto Condensed", "Arial Narrow", sans-serif;
  }
  .card {
    position: absolute; left: 250px; width: 700px; height: 400px;
    background: linear-gradient(115deg, var(--green-light) 0%, var(--green-dark) 100%);
    overflow: hidden;
  }
  .card--front { top: 147px; }
  .card--back { top: 652px; }
  .card__shapes { position: absolute; inset: 0; }

  .brand {
    position: absolute; display: flex; align-items: center; gap: 10px;
    font-weight: 700; letter-spacing: 2px; text-transform: uppercase;
    transform: translate(-50%, -50%); white-space: nowrap;
  }
  .brand__mark { width: 20px; height: 20px; flex: none; }
  .brand--front { left: 50%; top: 50%; color: #ffffff; font-size: 54px; }
  .brand--front .brand__mark { background: #ffffff; }
  .brand--back { left: 160px; top: 211px; color: var(--ink); font-size: 42px; }
  .brand--back .brand__mark { background: var(--green-light); }

  .holder { position: absolute; left: 419px; top: 70px; color: var(--ink); white-space: nowrap; }
  .holder__name { font-size: 26px; font-weight: 700; letter-spacing: 3.5px; text-transform: uppercase; }
  .holder__title { margin-top: 8px; font-size: 19px; font-weight: 500; letter-spacing: 1.5px; }

  .contacts { position: absolute; left: 419px; top: 273px; list-style: none; color: var(--ink);
    font-size: 19px; font-weight: 500; letter-spacing: 1.5px; line-height: 26.5px; white-space: nowrap; }
</style>
</head>
<body>
  <section class="card card--front" aria-label="Card front">
    <div class="brand brand--front"><span class="brand__mark"></span>Quillmere</div>
  </section>

  <section class="card card--back" aria-label="Card back">
    <svg class="card__shapes" viewBox="0 0 700 400" width="700" height="400" aria-hidden="true">
      <path class="panel-white" d="M0 0 H250 Q416 200 254 400 H0 Z" fill="var(--paper)"/>
      <path class="panel-band" d="M250 0 H294 Q470 200 283 400 H254 Q416 200 250 0 Z" fill="var(--band)"/>
    </svg>
    <div class="brand brand--back"><span class="brand__mark"></span>Quillmere</div>
    <div class="holder">
      <p class="holder__name">Lukas Varenko</p>
      <p class="holder__title">Fund Manager</p>
    </div>
    <ul class="contacts">
      <li>T: +1 555 284 6190</li>
      <li>E: lv@FundQuillmere.com</li>
      <li>W: www.FundQuillmere.com</li>
    </ul>
  </section>
</body>
</html>
```